Wordpress template for a mens-choire webpage

Task is to design a Wordpress template for an 98 years old estonian mens choire webpage.
Design should involve details from the attached files, choire logo and the colors of the choire flag: in horizontal orientation bright sky-blue, white, bright grass-green.
Designer signature is allowed to be added to the template, with country of origin.

Reason: Deadline extended 2 days (until 2. March 2014) to accommodate designers creativity.

Thank you everyone for your great designs!
Our project has now entered into a voting and decision phase until 14th of March 2014 (included).

```html
<!DOCTYPE html>
<html lang="en">
<head>
<meta charset="utf-8">
<title>Lindvere Choir</title>
<link href="https://fonts.googleapis.com/css2?family=Ubuntu:wght@400;500&display=swap" rel="stylesheet">
<style>
:root{
  --green:#6aab34;
  --sky:#1f64a8;
  --navy:#1b2a8f;
  --nav-top:#2a3fc4;
  --nav-bottom:#1a2a9e;
  --accent:#f0a030;
  --text:#333;
  --muted:#555;
  --line:#d6d6d6;
  --panel:#f6f6f6;
}
*{box-sizing:border-box;margin:0;padding:0}
html,body{width:762px;height:1200px;overflow:hidden}
body{position:relative;font-family:'Ubuntu',sans-serif;color:var(--text);background:#fff}
.backdrop{position:absolute;inset:0}
.page{position:absolute;left:48px;top:53px;width:662px;height:1099px;background:#fff;box-shadow:0 1px 4px rgba(0,0,0,.25)}
.abs{position:absolute}
.brand{left:28px;top:40px;display:flex;align-items:center;gap:8px}
.brand-mark{width:20px;height:20px;border-radius:50%;background:var(--navy)}
.brand-name{font-size:15px;font-weight:500;color:var(--navy)}
.search{left:468px;top:44px;width:168px;height:26px;border:1px solid #bbb;border-radius:2px;box-shadow:inset 0 1px 2px rgba(0,0,0,.1);font-size:9px;color:#888;padding:8px 10px}
.search svg{position:absolute;right:5px;top:4px}
.nav{left:28px;top:101px;width:608px;height:40px;border-radius:3px;background:linear-gradient(var(--nav-top),var(--nav-bottom));display:flex;align-items:center;padding-left:19px;gap:21px}
.nav a{color:#fff;font-size:9.5px;text-decoration:none}
.nav a.current{color:var(--accent)}
.hero{left:28px;top:151px;width:608px;height:246px;border-radius:3px;background:linear-gradient(#8a5a2a 0%,#5a3a20 40%,#1a1414 75%,#111 100%)}
.hero-caption{left:27px;top:316px;width:234px;height:38px;background:rgba(255,255,255,.95);font-size:16px;color:var(--navy);padding:9px 0 0 27px}
.dots{left:319px;top:376px;display:flex;gap:6px}
.dots i{width:7px;height:7px;border-radius:50%;background:#fff}
.dots i.on{background:#4a5ad8}
.col{width:190px;top:421px}
.col-release{left:28px}
.col-events{left:237px}
.col-team{left:446px}
.col-rule{height:3px;background:var(--navy)}
.col-head{display:flex;justify-content:space-between;margin-top:15px;font-size:12px;color:var(--navy);font-weight:500}
.arrows{font-size:11px;letter-spacing:2px}
.col-img{height:96px;margin-top:16px;border:1px solid #444}
.col-title{margin-top:18px;font-size:10.5px;color:var(--navy);font-weight:500}
.col-text{margin-top:4px;font-size:7.5px;line-height:19px;color:var(--muted);text-align:justify}
.divider{left:28px;top:685px;width:608px;height:1px;background:var(--line)}
.video-head{left:28px;top:713px;width:392px;display:flex;justify-content:space-between;font-size:12px;color:var(--navy);font-weight:500}
.video{left:28px;top:741px;width:393px;height:240px;background:radial-gradient(ellipse at 50% 25%,#6a5ad0 0%,#3a2a70 35%,#3a2440 60%,#1a1020 100%)}
.video-bar{left:0;top:0;width:100%;height:20px;background:rgba(0,0,0,.85);color:#fff;font-size:8px;padding:5px 8px}
.video-play{left:170px;top:100px;width:54px;height:36px;border-radius:8px;background:rgba(20,20,20,.85)}
.video-controls{left:0;bottom:0;width:100%;height:22px;background:#111;color:#ccc;font-size:6.5px;padding:9px 0 0 58px}
.video-track{left:0;bottom:22px;width:100%;height:3px;background:#555}
.concerts{left:447px;top:713px;width:189px;height:268px;border:1px solid var(--line);padding:0 12px}
.concerts-head{display:flex;justify-content:space-between;margin-top:16px;font-size:12px;color:var(--navy);font-weight:500}
.concert-img{height:66px;margin-top:10px}
.concert-text{margin-top:8px;font-size:7.5px;line-height:15px;color:var(--muted);text-align:justify;text-align-last:justify}
.footer{left:28px;top:1009px;width:608px;height:56px;border:1px solid var(--line);background:var(--panel)}
.footer-links{left:144px;top:15px;display:flex;gap:17px;font-size:7.5px;color:var(--navy)}
.copyright{left:0;top:31px;width:608px;text-align:center;font-size:7.5px;color:var(--navy)}
.social{left:517px;top:19px;display:flex;gap:12px}
.social i{width:14px;height:14px;border-radius:2px}
</style>
</head>
<body>
<svg class="backdrop" width="762" height="1200" viewBox="0 0 762 1200" aria-hidden="true">
  <defs>
    <radialGradient id="glow" cx="0.5" cy="0" r="0.4"><stop offset="0" stop-color="#9fd070"/><stop offset="1" stop-color="#6aab34"/></radialGradient>
    <linearGradient id="sea" x1="0" y1="0" x2="0" y2="1"><stop offset="0" stop-color="#2470b4"/><stop offset="1" stop-color="#164f8c"/></linearGradient>
  </defs>
  <rect width="762" height="1200" fill="#efefef"/>
  <polygon points="0,0 762,0 762,135 0,202" fill="url(#glow)"/>
  <polygon points="0,622 762,470 762,1200 0,1200" fill="url(#sea)"/>
</svg>

<main class="page">
  <div class="abs brand"><span class="brand-mark"></span><span class="brand-name">Lindvere Choir</span></div>
  <div class="abs search">search...
    <svg width="18" height="18" viewBox="0 0 18 18"><circle cx="7" cy="7" r="5" fill="none" stroke="#555" stroke-width="2"/><line x1="11" y1="11" x2="16" y2="16" stroke="#555" stroke-width="2.5"/></svg>
  </div>

  <nav class="abs nav">
    <a class="current">Home</a><a>About us</a><a>Latest Events</a><a>PhotoGallery</a><a>Arrangements</a><a>Contact us</a>
  </nav>

  <div class="abs hero" role="img" aria-label="Men's choir group photo in a wood-panelled concert hall"></div>
  <div class="abs hero-caption">98 Years of Estonian Choire</div>
  <div class="abs dots"><i class="on"></i><i></i><i></i></div>

  <section class="abs col col-release">
    <div class="col-rule"></div>
    <div class="col-head"><span>Latest Release</span><span class="arrows">‹ ›</span></div>
    <div class="col-img" role="img" aria-label="Singers in tuxedos standing in a row under a cloudy sky" style="background:linear-gradient(#8a8f96,#c8ccd0 60%,#333 100%)"></div>
    <div class="col-title">Lorem ipsum dolor</div>
    <p class="col-text">Lorem ipsum dolor sit amet, consectetur adipisicing elit, sed do eiusmod tempor incididunt ut labore et dolore magna aliqua.</p>
  </section>
  <section class="abs col col-events">
    <div class="col-rule"></div>
    <div class="col-head"><span>Event Arrangement</span><span class="arrows">‹ ›</span></div>
    <div class="col-img" role="img" aria-label="Choir performing in a church" style="background:linear-gradient(#7a8aa8,#3a3a40 45%,#1a1a1a 100%)"></div>
    <div class="col-title">Lorem ipsum dolor</div>
    <p class="col-text">Lorem ipsum dolor sit amet, consectetur adipisicing elit, sed do eiusmod tempor incididunt ut labore et dolore magna aliqua.</p>
  </section>
  <section class="abs col col-team">
    <div class="col-rule"></div>
    <div class="col-head"><span>Our Team</span><span class="arrows">‹ ›</span></div>
    <div class="col-img" role="img" aria-label="Close group of choir members in dark suits" style="background:linear-gradient(135deg,#2a2a2a,#8a8a8a 50%,#222)"></div>
    <div class="col-title">Lorem ipsum dolor</div>
    <p class="col-text">Lorem ipsum dolor sit amet, consectetur adipisicing elit, sed do eiusmod tempor incididunt ut labore et dolore magna aliqua.</p>
  </section>

  <div class="abs divider"></div>

  <div class="abs video-head"><span>Latest Video</span><span class="arrows">‹ ›</span></div>
  <div class="abs video" role="img" aria-label="Concert crowd under stage lights">
    <div class="abs video-bar">Night Arena Mix (HD VERSION)</div>
    <div class="abs video-play"><svg width="54" height="36" viewBox="0 0 54 36"><polygon points="22,11 34,18 22,25" fill="#fff"/></svg></div>
    <div class="abs video-track"></div>
    <div class="abs video-controls">0:00 / 8:25</div>
  </div>

  <aside class="abs concerts">
    <div class="concerts-head"><span>Upcoming Concerts</span><span class="arrows">‹ ›</span></div>
    <div class="concert-img" role="img" aria-label="Choir singing with music folders" style="background:linear-gradient(#2a2a30,#6a6a70 50%,#1a1a1a)"></div>
    <p class="concert-text">Lorem ipsum dolor sit amet, consectetur adipisicing elit, sed do eiusmod tempor</p>
    <div class="concert-img" role="img" aria-label="Small vocal group in suits" style="background:linear-gradient(#6a3a20,#3a2418 50%,#151515)"></div>
    <p class="concert-text">Lorem ipsum dolor sit amet, consectetur adipisicing elit, sed do eiusmod tempor</p>
  </aside>

  <footer class="abs footer">
    <div class="abs footer-links"><span>Home</span><span>About us</span><span>Latest Events</span><span>PhotoGallery</span><span>Arrangements</span><span>Contact us</span></div>
    <div class="abs copyright">© 2013 - 2014 Company name. All rights reserved</div>
    <div class="abs social"><i style="background:#3b5998"></i><i style="background:#3ab0e0"></i><i style="background:#f08a20"></i></div>
  </footer>
</main>
</body>
</html>
```